Business Card Design for BrightvaleMedia.com

--I need a business card design for my company BrightvaleMedia.com

I have attached my logo...I want the brightvale media logo on the front of the business card, and then I want The Quillstone Chief on the back of it with my information.

I would like to see a light colored background as well as a dark colored background

FRONT:
BRIGHTVALE MEDIA LOGO
248 N. Larkmoor
3rd Floor
San Diego CA 92173
www.BrightvaleMedia.com

Advanced Website & App Development
Websites, Apps, Online Voucher Systems

Leading Edge Marketing Services
SMS, VB, SMM, SEM,

BACK:
QUILLSTONE CHIEF LOGO
Dorian Pelletta
The Quillstone Chief
Call Or Text: 619-555-0148
Dorian@QuillstoneChief.example
www.QuillstoneChief.example

Target Market(s)

small business owners

Industry/Entity Type

Business Consultant

Contact Information for Business Card

FRONT:
BRIGHTVALE MEDIA LOGO
248 N. Larkmoor
3rd Floor
San Diego CA 92173
www.BrightvaleMedia.com

SMS, VB, SMM, SEM,

BACK:
QUILLSTONE CHIEF LOGO
Dorian Pelletta
The Quillstone Chief
Dorian@QuillstoneChief.example
www.QuillstoneChief.example

Requirements
Must have
• add this quote on it somewhere, anywhere,preferrably on back
• "The Fastest Way To Success Is To Take Action”
• — Dorian Pelletta, Quillstone Chief
Nice to have
• open
Should not have
• red

```html
<!DOCTYPE html>
<html lang="en">
<head>
<meta charset="utf-8">
<title>Brightvale Media Business Card</title>
<link rel="stylesheet" href="https://fonts.googleapis.com/css2?family=Source+Sans+3:ital,wght@0,400;0,600;0,700;1,400&display=swap">
<style>
  :root {
    --brand-blue: #0071a8;
    --brand-gray: #6d6e70;
    --text-gray: #5a5b5d;
    --card-white: #ffffff;
    --stage: #e8e9eb;
  }
  * { box-sizing: border-box; margin: 0; padding: 0; }
  html, body {
    width: 1105px;
    height: 1200px;
    overflow: hidden;
    background: var(--stage);
    font-family: "Source Sans 3", "Myriad Pro", Arial, sans-serif;
  }
  .canvas { position: relative; width: 1105px; height: 1200px; }
  .card {
    position: absolute;
    left: 196px;
    width: 720px;
    height: 411px;
  }
  .card--front { top: 146px; background: var(--brand-blue); color: var(--card-white); }
  .card--back { top: 602px; background: var(--card-white); }

  .wordmark {
    position: absolute;
    left: 59px;
    font-weight: 600;
    letter-spacing: 3px;
    text-transform: uppercase;
    line-height: 1;
  }
  .card--front .wordmark { top: 63px; font-size: 34px; color: var(--card-white); }
  .card--back .wordmark { top: 63px; font-size: 38px; color: var(--brand-blue); }

  .info-block {
    position: absolute;
    left: 59px;
    font-size: 19.5px;
    line-height: 26px;
  }
  .info-block--address { top: 140px; }
  .info-block--dev { top: 234px; }
  .info-block--marketing { top: 299px; }
  .info-block .web { font-weight: 700; }
  .sep { margin: 0 3px; }

  .quote {
    position: absolute;
    left: 59px;
    top: 140px;
    width: 600px;
    color: var(--text-gray);
  }
  .quote__text {
    font-size: 18px;
    font-style: italic;
    line-height: 24px;
  }
  .quote__source {
    font-size: 15px;
    line-height: 22px;
    color: var(--brand-gray);
  }

  .holder {
    position: absolute;
    left: 52px;
    top: 270px;
  }
  .holder__name {
    font-size: 27px;
    font-weight: 600;
    color: var(--brand-blue);
    line-height: 32px;
  }
  .holder__title {
    font-size: 20px;
    color: var(--text-gray);
    line-height: 26px;
  }

  .contacts {
    position: absolute;
    left: 400px;
    top: 272px;
    list-style: none;
  }
  .contacts li {
    display: flex;
    align-items: center;
    height: 27.5px;
    font-size: 19px;
    color: var(--text-gray);
  }
  .contacts svg { width: 17px; height: 17px; margin-right: 13px; fill: var(--brand-blue); flex: none; }

  .footer-band {
    position: absolute;
    left: 0;
    bottom: 0;
    width: 100%;
    height: 18px;
    display: flex;
  }
  .footer-band__blue { width: 533px; background: var(--brand-blue); }
  .footer-band__gap { width: 4px; background: var(--card-white); }
  .footer-band__gray { flex: 1; background: var(--brand-gray); }
</style>
</head>
<body>
<main class="canvas">

  <section class="card card--front" aria-label="Card front">
    <div class="wordmark">Brightvale Media</div>
    <p class="info-block info-block--address">
      248 N. Larkmoor, 3rd Floor<br>
      San Diego CA 92173<br>
      <span class="web">www.BrightvaleMedia.com</span>
    </p>
    <p class="info-block info-block--dev">
      Advanced Website &amp; App Development<br>
      Websites<span class="sep">•</span>Apps<span class="sep">•</span>Online Voucher Systems
    </p>
    <p class="info-block info-block--marketing">
      Leading Edge Marketing Services<br>
      SMS<span class="sep">•</span>VB<span class="sep">•</span>SMM<span class="sep">•</span>SEM
    </p>
  </section>

  <section class="card card--back" aria-label="Card back">
    <div class="wordmark">Quillstone Chief</div>

    <blockquote class="quote">
      <p class="quote__text">“The Fastest Way To Success Is To Take Action”</p>
      <p class="quote__source">— Dorian Pelletta, Quillstone Chief</p>
    </blockquote>

    <div class="holder">
      <p class="holder__name">Dorian Pelletta</p>
      <p class="holder__title">The Quillstone Chief</p>
    </div>

    <ul class="contacts">
      <li>
        <svg viewBox="0 0 24 24" aria-hidden="true"><path d="M6.6 10.8a15.1 15.1 0 0 0 6.6 6.6l2.2-2.2c.3-.3.7-.4 1-.2 1.1.4 2.3.6 3.6.6.6 0 1 .4 1 1V20c0 .6-.4 1-1 1C10.6 21 3 13.4 3 4c0-.6.4-1 1-1h3.5c.6 0 1 .4 1 1 0 1.3.2 2.5.6 3.6.1.3 0 .7-.2 1z"/></svg>
        619-555-0148
      </li>
      <li>
        <svg viewBox="0 0 24 24" aria-hidden="true"><path d="M2 5h20v2l-10 6L2 7z"/><path d="M2 9l10 6 10-6v10H2z"/></svg>
        Dorian@QuillstoneChief.example
      </li>
      <li>
        <svg viewBox="0 0 24 24" aria-hidden="true"><circle cx="12" cy="12" r="10"/><g stroke="#fff" stroke-width="1.4" fill="none"><ellipse cx="12" cy="12" rx="4" ry="9.5"/><path d="M2.5 12h19M4 7h16M4 17h16"/></g></svg>
        www.QuillstoneChief.example
      </li>
    </ul>

    <div class="footer-band" aria-hidden="true">
      <span class="footer-band__blue"></span>
      <span class="footer-band__gap"></span>
      <span class="footer-band__gray"></span>
    </div>
  </section>

</main>
</body>
</html>
```